Stationary Suite for Aussie Law Firm

We are a small law firm operating out of Albany, Western Australia. We have a logo, which we love and was the winner of a ArtworkHive contest last year.
We require a suite of business stationary products incorporating our logo and contact details. These should be:
1. Letterhead (A4)
The letterhead should incorporate the following information in addition to the logo:
ABN 38 602 917 255 (this is our Australian Business Number)
Beatrix Lund atf The BJL Legal Trust t/as Harbour Gate Legal & Conveyancing (legal name of the business)
Address: Wexley House, Wexley Street, Albany
Postal Address: PO Box 8147, Albany WA 6332
Telephone: 0491 670 382
Facsimile: 08 9722 5913
Email: info@harbourgatelegal.com.au
Website: www.harbourgatelegal.com.au
2. Business Card (90mm x 55mm)
I've attached my current business card layout just for your information.
The front of the business card should include the following information in addition to the logo:
Beatrix Lund
Director & Principal Solicitor
Telephone: 0491 670 382
Facsimile: 08 9722 5913
Email: beatrix@harbourgatelegal.com.au
The back of the card should be similar to the back of my existing card, but should only have the logo in white and the address of our website (www.harbourgatelegal.com.au)
3. Email signature block
This should include the same information as the front of the business card.
4. With Compliments slip (DL size)
The With Compliments slip should include the same information as the Letterhead.
5. Banner (830mm x 2000mm)
We need a banner designed for use at marketing events. This should include our website details and logo - other than that you have fairly free reign with the design.
6. Flyer (DL)
We need a flyer setting out our services and main contact details for use at marketing events. The details to be included are:
Telephone: 0491 670 382
Web: www.harbourgatelegal.com.au
Areas of law:
Wills & Estate Planning
Probate & Letters of Administration
Property Law & Conveyancing
General Commercial Law
Business Law
Style guide:
Please look at our website for an idea as to the style of designs we are looking for - www.harbourgatelegal.com.au. The design should be modern, sharp and professional.
Colours:
The CMYK details for the colours in our logo are:
Light Blue C72 M5 Y0 K0
Dark Blue C97 M72 Y16 K30
Edit 31/7/2014
I have added a couple of photos that we have used on our website, and additional photos. These are from our local area, so feel free to use these in your designs or to inform them.
- Calibri, Century Gothic

```html
<!DOCTYPE html>
<html lang="en">
<head>
<meta charset="utf-8">
<title>Harbour Gate Legal &amp; Conveyancing – Stationery Suite</title>
<link rel="stylesheet" href="https://fonts.googleapis.com/css2?family=Lato:wght@400;700&display=swap">
<style>
  :root {
    --sky: #3aaee2;
    --navy: #1d4c7e;
    --ink: #2a2a2a;
    --paper: #ffffff;
    --mist: #ededed;
    --stage: #e4e4e4;
  }
  * { box-sizing: border-box; margin: 0; padding: 0; }
  html, body { width: 1200px; height: 770px; overflow: hidden; }
  body {
    background: var(--stage);
    font-family: "Lato", Arial, sans-serif;
    color: var(--ink);
    position: relative;
  }
  .piece { position: absolute; background: var(--paper); overflow: hidden; box-shadow: 0 2px 6px rgba(0,0,0,.18); }
  .piece > svg.wave { position: absolute; left: 0; width: 100%; display: block; }

  .wordmark { display: flex; align-items: center; gap: 6px; color: var(--navy); font-weight: 400; line-height: 1.05; text-transform: uppercase; }
  .wordmark .dot { width: 10px; height: 10px; border-radius: 50%; background: var(--sky); flex: none; }
  .wordmark.on-blue { color: #fff; }
  .wordmark.on-blue .dot { background: #fff; }

  /* Business card front */
  .card-front { left: 66px; top: 62px; width: 158px; height: 100px; }
  .card-front .wordmark { position: absolute; left: 8px; top: 12px; font-size: 7px; width: 96px; }
  .card-front .who { position: absolute; right: 8px; top: 32px; text-align: right; }
  .card-front .name { font-size: 7px; color: var(--ink); }
  .card-front .role { font-size: 4.2px; color: var(--sky); white-space: nowrap; }
  .card-front .contact { position: absolute; left: 102px; top: 54px; font-size: 6px; color: #fff; line-height: 1.3; white-space: nowrap; }
  .card-front .contact.email { left: 86px; top: 74px; font-size: 4.3px; }
  .card-front .address { position: absolute; left: 30px; top: 86px; font-size: 3.4px; color: #fff; line-height: 1.3; white-space: nowrap; }

  /* Business card back */
  .card-back { left: 66px; top: 222px; width: 158px; height: 100px; background: var(--sky); }
  .card-back .wordmark { position: absolute; left: 20px; top: 30px; font-size: 11px; width: 130px; }
  .card-back .web { position: absolute; left: 0; right: 0; bottom: 8px; text-align: center; font-size: 5.6px; color: var(--navy); }

  /* Email signature */
  .email-sig { left: 66px; top: 560px; width: 150px; height: 90px; padding: 10px 12px; }
  .email-sig .wordmark { font-size: 7px; margin-bottom: 6px; }
  .email-sig p { font-size: 4.6px; line-height: 1.45; color: #3b5b80; }
  .email-sig .name { font-weight: 700; font-size: 5.4px; color: var(--navy); }
  .email-sig .muted { color: #9aa5b2; }

  /* Letterhead */
  .letterhead { left: 325px; top: 92px; width: 380px; height: 540px; }
  .letterhead > svg.wave { top: 0; height: 130px; }
  .letterhead .wordmark { position: absolute; left: 42px; top: 60px; font-size: 15px; width: 170px; }
  .letterhead .lines { position: absolute; right: 36px; top: 100px; text-align: right; font-size: 5.6px; line-height: 1.5; }
  .letterhead .letter { position: absolute; left: 40px; right: 40px; top: 160px; font-size: 6.5px; line-height: 1.6; text-align: justify; }
  .letterhead .salute { font-size: 12px; margin-bottom: 16px; }
  .letterhead .letter p { margin-bottom: 9px; }
  .letterhead .signoff { position: absolute; left: 266px; top: 420px; font-size: 6.5px; }
  .letterhead .signature { display: block; width: 60px; height: 18px; margin-top: 4px; background: linear-gradient(90deg, #e8ecf4, #d4dcec); }
  .letterhead .legal { position: absolute; left: 0; right: 0; top: 491px; text-align: center; font-size: 5.4px; line-height: 1.5; }
  .letterhead .foot { position: absolute; top: 511px; font-size: 5.2px; line-height: 1.5; }
  .letterhead .foot.left { left: 28px; }
  .letterhead .foot.right { right: 28px; }

  /* With compliments slip */
  .compliments { left: 767px; top: 82px; width: 430px; height: 182px; }
  .compliments > svg.wave { bottom: 0; height: 80px; }
  .compliments .wordmark { position: absolute; left: 14px; top: 16px; font-size: 11px; width: 130px; }
  .compliments h1 { position: absolute; left: 0; right: 0; top: 80px; text-align: center; font-weight: 400; font-size: 16px; color: var(--navy); letter-spacing: .3px; }
  .compliments .legal { position: absolute; left: 0; right: 0; top: 136px; text-align: center; font-size: 4.6px; line-height: 1.45; color: #fff; }
  .compliments .foot { position: absolute; top: 158px; font-size: 4.8px; line-height: 1.5; color: #fff; white-space: nowrap; }
  .compliments .foot b { font-weight: 700; }
  .compliments .foot.c1 { left: 44px; }
  .compliments .foot.c2 { left: 162px; }
  .compliments .foot.c3 { left: 246px; }

  /* Flyer */
  .flyer { left: 767px; top: 400px; width: 430px; height: 203px; }
  .flyer > svg.wave { top: 0; height: 203px; }
  .flyer .wordmark { position: absolute; left: 14px; top: 16px; font-size: 10px; width: 120px; }
  .flyer .services { position: absolute; right: 26px; top: 42px; text-align: right; list-style: none; color: #fff; font-size: 13px; line-height: 1.25; white-space: nowrap; }
  .flyer .phone { position: absolute; right: 26px; top: 132px; color: #fff; font-size: 11px; }
  .flyer .band-text { position: absolute; left: 14px; right: 26px; top: 178px; display: flex; justify-content: space-between; color: #fff; font-size: 8.5px; }
</style>
</head>
<body>

<section class="piece card-front" aria-label="Business card front">
  <svg class="wave" style="top:0;height:100px" viewBox="0 0 158 100" preserveAspectRatio="none" aria-hidden="true">
    <path d="M0 66 C40 52 90 40 158 46 L158 100 L0 100 Z" fill="var(--sky)"/>
  </svg>
  <div class="wordmark"><span class="dot"></span>Harbour Gate Legal &amp; Conveyancing</div>
  <div class="who">
    <div class="name">Beatrix Lund</div>
    <div class="role">Director &amp; Principal Solicitor</div>
  </div>
  <div class="contact">t: 0491 670 382<br>f: 08 9722 5913</div>
  <div class="contact email">e: beatrix@harbourgatelegal.com.au</div>
  <div class="address">Wexley House, Wexley Street, Albany<br>PO Box 8147, Albany WA 6332</div>
</section>

<section class="piece card-back" aria-label="Business card back">
  <svg class="wave" style="bottom:0;height:36px" viewBox="0 0 158 36" preserveAspectRatio="none" aria-hidden="true">
    <path d="M0 14 C50 2 100 0 158 10 L158 36 L0 36 Z" fill="#fff"/>
  </svg>
  <div class="wordmark on-blue"><span class="dot"></span>Harbour Gate Legal &amp; Conveyancing</div>
  <div class="web">www.harbourgatelegal.com.au</div>
</section>

<section class="piece email-sig" aria-label="Email signature">
  <div class="wordmark"><span class="dot"></span>Harbour Gate Legal &amp; Conveyancing</div>
  <p class="name">Beatrix Lund</p>
  <p>Director &amp; Principal Solicitor</p>
  <p>t: 0491 670 382 &nbsp;f: 08 9722 5913</p>
  <p>e: beatrix@harbourgatelegal.com.au</p>
  <p class="muted">Wexley House, Wexley Street, Albany<br>PO Box 8147, Albany WA 6332</p>
</section>

<section class="piece letterhead" aria-label="Letterhead">
  <svg class="wave" viewBox="0 0 380 130" preserveAspectRatio="none" aria-hidden="true">
    <path d="M0 0 L380 0 L380 62 C300 50 250 80 200 110 C150 135 60 128 0 110 Z" fill="var(--mist)"/>
  </svg>
  <div class="wordmark"><span class="dot"></span>Harbour Gate Legal &amp; Conveyancing</div>
  <div class="lines">Telephone: 0491 670 382<br>Facsimile: 08 9722 5913</div>
  <div class="letter">
    <p class="salute">Dear Mr. Hollis,</p>
    <p>Lorem ipsum dolor sit amet, consectetur adipiscing elit. Donec orci purus, luctus vitae dignissim eu, iaculis sed purus. Vivamus faucibus, ipsum nec aliquet viverra, leo mauris condimentum ligula, sit amet sagittis enim ligula quis arcu. Nam egestas tortor id nisi porttitor mattis. In tortor ante, ultricies in suscipit a, tempus non massa. Vivamus et auctor mi. Fusce vel massa nulla. Phasellus nec eros mauris, et scelerisque orci.</p>
    <p>Donec malesuada orci vitae nulla accumsan porta a id massa. Quisque accumsan iaculis magna sit amet fringilla. Maecenas consequat, magna eget tincidunt semper, odio nibh rutrum mi, id feugiat ante nisi eu risus. Vestibulum nunc orci, rhoncus a placerat in, ultricies in mi. Cras mattis varius eros, vel fringilla nisi suscipit eget. Quisque scelerisque sagittis nulla at porttitor.</p>
    <p>Sed id augue vitae urna euismod commodo aliquet a quam. Pellentesque arcu velit, cursus et malesuada ut, consequat et diam. Nullam erat sem, rhoncus id ullamcorper vitae, rhoncus et arcu. In ultricies ultricies nulla, ut rutrum nisi iaculis at. Donec eu magna a metus ornare faucibus. Fusce aliquet faucibus ultricies. Morbi semper, est id tincidunt gravida, sem arcu adipiscing lacus, ac bibendum nulla leo eu purus. Quisque nec diam sed risus consectetur a accumsan quis nibh. Vestibulum id purus lorem.</p>
  </div>
  <div class="signoff">Sincerely,<span class="signature" role="img" aria-label="Handwritten signature"></span></div>
  <div class="legal">ABN 38 602 917 255<br>Beatrix Lund atf The BJL Legal Trust t/as Harbour Gate Legal &amp; Conveyancing</div>
  <div class="foot left">Address: Wexley House, Wexley Street, Albany<br>Postal Address: PO Box 8147, Albany WA 6332</div>
  <div class="foot right">Email: info@harbourgatelegal.com.au<br>Website: www.harbourgatelegal.com.au</div>
</section>

<section class="piece compliments" aria-label="With compliments slip">
  <svg class="wave" viewBox="0 0 430 80" preserveAspectRatio="none" aria-hidden="true">
    <path d="M0 34 C120 30 260 28 330 18 C370 12 400 6 430 0 L430 80 L0 80 Z" fill="var(--sky)"/>
  </svg>
  <div class="wordmark"><span class="dot"></span>Harbour Gate Legal &amp; Conveyancing</div>
  <h1>WITH COMPLIMENTS</h1>
  <div class="legal">ABN 38 602 917 255<br>Beatrix Lund atf The BJL Legal Trust t/as Harbour Gate Legal &amp; Conveyancing</div>
  <div class="foot c1"><b>Email:</b> info@harbourgatelegal.com.au<br><b>Website:</b> www.harbourgatelegal.com.au</div>
  <div class="foot c2"><b>Telephone:</b> 0491 670 382<br><b>Facsimile:</b> 08 9722 5913</div>
  <div class="foot c3"><b>Address:</b> Wexley House, Wexley Street, Albany<br><b>Postal Address:</b> PO Box 8147, Albany WA 6332</div>
</section>

<section class="piece flyer" aria-label="Services flyer">
  <svg class="wave" viewBox="0 0 430 203" preserveAspectRatio="none" aria-hidden="true">
    <path d="M0 62 C100 44 220 26 430 6 L430 203 L0 203 Z" fill="var(--sky)"/>
    <rect x="0" y="168" width="430" height="35" fill="var(--navy)"/>
    <rect x="0" y="163" width="430" height="5" fill="#fff"/>
  </svg>
  <div class="wordmark"><span class="dot"></span>Harbour Gate Legal &amp; Conveyancing</div>
  <ul class="services">
    <li>Wills &amp; Estate Planning</li>
    <li>Probate &amp; Letters of Administration</li>
    <li>Property Law &amp; Conveyancing</li>
    <li>General Commercial Law</li>
    <li>Business Law</li>
  </ul>
  <div class="phone">Telephone: 0491 670 382</div>
  <div class="band-text"><span>info@harbourgatelegal.com.au</span><span>www.harbourgatelegal.com.au</span></div>
</section>

</body>
</html>
```